Super elegant, crisp & clean Business card design required

We recently upgraded our branding - which is on our website - talvendoraphoto.com

I would like a simple, yet elegant, clean business card design please.

The font of my logo is Cinzel - and because of the natural colour - it's best to have this on a black background.

I would like to have the back of the business card - with simply my logo.

PLEASE DO NOT SUBMIT A COMPLICATED / UNCLEAN DESIGN

Industry/Entity Type

Business

Contact Information for Business Card

Talven Doroshko Photography

Font styles to use
Other font styles liked:
• Cinzel

Requirements
Must have
• A backpage with nothing but my logo
• Simple design - stands out
Should not have
• Colour that dont align with my logo
• Over complicated '/ non symmetrical design

```html
<!DOCTYPE html>
<html lang="en">
<head>
<meta charset="utf-8">
<title>Talven Doroshko Photography – Business Card</title>
<link href="https://fonts.googleapis.com/css2?family=Cinzel:wght@400&family=Open+Sans:wght@400&display=swap" rel="stylesheet">
<style>
  :root {
    --backdrop: #e6e6e6;
    --card: #000000;
    --card-back: #0d0d0d;
    --card-pattern: #141414;
    --gold: #a38f6c;
    --white: #ffffff;
    --grey: #b9b9b9;
  }
  * { margin: 0; padding: 0; box-sizing: border-box; }
  html, body { width: 1200px; height: 900px; overflow: hidden; }
  body {
    background: var(--backdrop);
    position: relative;
    font-family: "Open Sans", Arial, sans-serif;
  }
  .card {
    position: absolute;
    top: 306px;
    width: 440px;
    height: 271px;
    border-radius: 10px;
    overflow: hidden;
  }
  .card--front { left: 149px; background: var(--card); }
  .card--back { left: 608px; background: var(--card-back); }

  .brand-name {
    font-family: "Cinzel", Georgia, serif;
    font-weight: 400;
    color: var(--gold);
  }
  .front-brand {
    position: absolute;
    left: 40px;
    top: 100px;
    width: 150px;
    text-align: center;
    font-size: 19px;
    line-height: 26px;
  }

  .contact {
    position: absolute;
    left: 226px;
    top: 60px;
  }
  .contact__name {
    font-family: "Cinzel", Georgia, serif;
    color: var(--gold);
    font-size: 19px;
    line-height: 22px;
    letter-spacing: 0.3px;
  }
  .contact__role {
    color: var(--white);
    font-size: 12px;
    line-height: 16px;
  }
  .contact__lines { list-style: none; margin-top: 16px; }
  .contact__lines li {
    display: flex;
    align-items: center;
    color: var(--grey);
    font-size: 12px;
    line-height: 16px;
  }
  .contact__lines svg { width: 9px; height: 9px; margin-right: 7px; fill: var(--gold); }
  .contact__address {
    margin-top: 13px;
    color: var(--white);
    font-size: 12px;
    line-height: 16px;
  }

  .back-pattern {
    position: absolute;
    inset: 0;
    background: linear-gradient(180deg, var(--card-pattern), var(--card-back));
  }
  .back-mark {
    position: absolute;
    left: 186px;
    top: 66px;
    width: 68px;
    height: 68px;
    border: 1px solid var(--gold);
    border-radius: 50%;
  }
  .back-brand {
    position: absolute;
    left: 0;
    right: 0;
    top: 172px;
    text-align: center;
  }
  .back-brand__name { font-size: 19px; line-height: 22px; letter-spacing: 0.5px; }
  .back-brand__tag { font-size: 8px; line-height: 12px; letter-spacing: 6px; }
  .back-brand__url {
    margin-top: 11px;
    color: var(--gold);
    font-size: 12px;
    line-height: 16px;
  }
</style>
</head>
<body>
  <section class="card card--front">
    <div class="brand-name front-brand">Talven<br>Doroshko</div>
    <div class="contact">
      <div class="contact__name">Elias Marwood</div>
      <div class="contact__role">Managing Director</div>
      <ul class="contact__lines">
        <li><svg viewBox="0 0 10 10"><path d="M1 4 Q5 0 9 4 L8 5 L6.5 4 L6.5 3.2 Q5 2.7 3.5 3.2 L3.5 4 L2 5 Z M2 6 H8 V9 H2 Z"/></svg>(044) 555 014 286</li>
        <li><svg viewBox="0 0 10 10"><path d="M3 0 H7 V3 H9 V10 H1 V3 H3 Z M4 1 V3 H6 V1 Z M3 5 V6 H7 V5 Z"/></svg>(044) 555014287</li>
        <li><svg viewBox="0 0 10 10"><path d="M0 2 H10 V3 L5 6 L0 3 Z M0 4 L5 7 L10 4 V8 H0 Z"/></svg>hello@talvendoraphoto.com</li>
      </ul>
      <div class="contact__address">27, Harrow Lane Studio,<br>Country, 40815</div>
    </div>
  </section>

  <section class="card card--back">
    <div class="back-pattern" role="img" aria-label="Subtle repeating monogram pattern across the card background"></div>
    <div class="back-mark"></div>
    <div class="back-brand">
      <div class="brand-name back-brand__name">Talven Doroshko</div>
      <div class="brand-name back-brand__tag">PHOTOGRAPHY</div>
      <div class="back-brand__url">www.talvendoraphoto.com</div>
    </div>
  </section>
</body>
</html>
```